Verodex business card

Business card for sustainable investment company called "Verodex". Verodex is an exchange platform selling carbon credits between buyers and sellers. Carbon Credits are an environmental commodity for reducing global carbon emissions.

the card should obviously have our logo and the theme should be sustainability/environment mixed with a trading platform.

Contact Information for Business Card

Logo, Name, Title, Phone, Email

Colors
0054AA
0677BA
7BADD7
CADEEF
E8F1F8
0094D4
00A9DD
6FCCEA
C7EBF8
E9F6FB
00AB8E
00BBA5
67D7C9
C6EFE9
E9F9F6
59FF00
82FF00
B8FF75
E3FFCB
F4FFEA

```html
<!DOCTYPE html>
<html lang="en">
<head>
<meta charset="utf-8">
<title>Verodex business card</title>
<link href="https://fonts.googleapis.com/css2?family=Raleway:wght@400;500;700&display=swap" rel="stylesheet">
<style>
  :root {
    --backdrop: #e6e9ee;
    --card: #0c2a55;
    --accent: #2aa9ea;
    --accent-light: #35c9f0;
    --text-light: #ffffff;
  }
  * { margin: 0; padding: 0; box-sizing: border-box; }
  html, body {
    width: 1200px; height: 977px; overflow: hidden;
    background: var(--backdrop);
    font-family: "Raleway", sans-serif;
  }
  .stage {
    width: 1200px; height: 977px;
    display: flex; align-items: center; justify-content: center; gap: 40px;
  }
  .card {
    position: relative;
    width: 540px; height: 370px;
    background: var(--card);
    border-radius: 26px;
    box-shadow: 0 10px 28px rgba(12, 42, 85, 0.25);
  }
  .card-front .brand {
    position: absolute; left: 0; right: 0; top: 50%;
    transform: translateY(-50%);
    display: flex; align-items: center; justify-content: center; gap: 22px;
  }
  .brand-dot {
    width: 58px; height: 58px; border-radius: 50%;
    background: var(--accent);
  }
  .brand-name {
    color: var(--text-light);
    font-weight: 700; font-size: 58px; letter-spacing: 1px;
  }
  .card-back .brand-corner {
    position: absolute; top: 40px; right: 42px;
    display: flex; align-items: center; gap: 10px;
  }
  .brand-corner .brand-dot { width: 26px; height: 26px; }
  .brand-corner .brand-name { font-size: 26px; color: var(--accent); }
  .holder {
    position: absolute; left: 46px; bottom: 40px;
  }
  .holder-name {
    color: var(--accent);
    font-weight: 700; font-size: 32px; letter-spacing: 0.5px; line-height: 1.1;
  }
  .holder-title {
    color: var(--text-light);
    font-weight: 500; font-size: 20px; margin-top: 6px;
  }
  .divider {
    width: 48px; height: 3px; background: var(--accent-light);
    margin: 18px 0 14px 12px;
  }
  .contact-list { list-style: none; }
  .contact-item {
    display: flex; align-items: center; gap: 12px;
    color: var(--text-light); font-size: 17px; font-weight: 500;
    margin-bottom: 6px; padding-left: 12px;
  }
  .contact-icon { width: 16px; height: 16px; flex: none; }
</style>
</head>
<body>
<main class="stage">
  <section class="card card-front">
    <div class="brand">
      <span class="brand-dot"></span>
      <span class="brand-name">VERODEX</span>
    </div>
  </section>

  <section class="card card-back">
    <div class="brand-corner">
      <span class="brand-dot"></span>
      <span class="brand-name">VERODEX</span>
    </div>
    <div class="holder">
      <h1 class="holder-name">MARCUS HALE</h1>
      <p class="holder-title">Founder &amp; CEO</p>
      <div class="divider"></div>
      <ul class="contact-list">
        <li class="contact-item">
          <svg class="contact-icon" viewBox="0 0 16 16"><path d="M3.5 1.5l2.3 2.6-1.3 1.8c.9 2 2.6 3.7 4.6 4.6l1.8-1.3 2.6 2.3-1.2 2.2C7 13.5 2.5 9 1.3 2.7z" fill="#2aa9ea"/></svg>
          <span>(555) 218-4470</span>
        </li>
        <li class="contact-item">
          <svg class="contact-icon" viewBox="0 0 16 16"><rect x="1" y="3" width="14" height="10" rx="1" fill="#2aa9ea"/><path d="M1.5 3.5L8 9l6.5-5.5" fill="none" stroke="#0c2a55" stroke-width="1.4"/></svg>
          <span>office@verodex.com</span>
        </li>
        <li class="contact-item">
          <svg class="contact-icon" viewBox="0 0 16 16"><circle cx="8" cy="8" r="6.5" fill="none" stroke="#2aa9ea" stroke-width="1.6"/><path d="M1.5 8h13M8 1.5c-2.6 3.5-2.6 9.5 0 13M8 1.5c2.6 3.5 2.6 9.5 0 13" fill="none" stroke="#2aa9ea" stroke-width="1.2"/></svg>
          <span>verodex.com</span>
        </li>
      </ul>
    </div>
  </section>
</main>
</body>
</html>
```